Looking for someone to design a business card for my plumbing business Quandor Plumbing Solutions I want the background also to be black, must attract clients. If possible I want the front to be the logo and the back to show maybe the details.

Target Market(s)

Clients

Industry/Entity Type

Plumbing maintenance

Contact Information for Business Card

Name: Felix, Contact: 0461 539 207, Email: quandorplumbingsolutions@mailbrook.example, Licence number 728093K

Font styles to use
Other font styles liked:
• as per logo maybe?

Colors

Designer to choose colors to be used in the design.

Requirements
Nice to have
• stating the service I provide, emergency plumbing, plumbing maintenance, drainage maintenance, block sewer and stormwater, camera and locating.

```html
<!DOCTYPE html>
<html lang="en">
<head>
<meta charset="utf-8">
<title>Quandor Plumbing Solutions – Business Card</title>
<link href="https://fonts.googleapis.com/css2?family=Montserrat:wght@400;500;800&display=swap" rel="stylesheet">
<style>
  :root {
    --stage: #3a3a3a;
    --brand-blue: #5096d3;
    --brand-blue-light: #8fbde6;
    --card-black: #141414;
    --ink-white: #ffffff;
    --ink-soft: #e8e8e8;
  }
  * { box-sizing: border-box; margin: 0; padding: 0; }
  html, body {
    width: 1200px;
    height: 689px;
    overflow: hidden;
    background: var(--stage);
    font-family: "Montserrat", Arial, sans-serif;
  }
  .canvas {
    position: relative;
    width: 1200px;
    height: 689px;
  }
  .card {
    position: absolute;
    top: 190px;
    width: 540px;
    height: 310px;
    border-radius: 22px;
    overflow: hidden;
  }
  .card--front {
    left: 40px;
    background: linear-gradient(100deg, var(--brand-blue-light) 0%, var(--brand-blue) 45%, var(--brand-blue) 100%);
  }
  .card--back {
    left: 620px;
    background: var(--card-black);
  }

  .brand {
    position: absolute;
    display: flex;
    align-items: center;
    gap: 14px;
  }
  .brand__dot {
    flex: none;
    border-radius: 50%;
  }
  .brand__name {
    font-weight: 800;
    text-transform: uppercase;
    line-height: 1.05;
  }
  .card--front .brand {
    left: 110px;
    top: 104px;
  }
  .card--front .brand__dot {
    width: 70px;
    height: 70px;
    background: var(--ink-white);
  }
  .card--front .brand__name {
    color: var(--ink-white);
    font-size: 30px;
  }
  .card--front .brand__name small {
    display: block;
    font-size: 15px;
    letter-spacing: 0.06em;
    font-weight: 800;
  }

  .card--back .brand {
    left: 26px;
    top: 176px;
    gap: 10px;
  }
  .card--back .brand__dot {
    width: 36px;
    height: 36px;
    background: var(--brand-blue);
  }
  .card--back .brand__name {
    color: var(--brand-blue);
    font-size: 17px;
  }
  .card--back .brand__name small {
    display: block;
    font-size: 9px;
    letter-spacing: 0.05em;
    font-weight: 800;
  }

  .divider {
    position: absolute;
    left: 236px;
    top: 72px;
    width: 2px;
    height: 170px;
    background: var(--brand-blue);
  }

  .details {
    position: absolute;
    left: 252px;
    top: 70px;
    right: 14px;
    color: var(--ink-soft);
  }
  .details__name {
    color: var(--brand-blue);
    font-weight: 800;
    font-size: 30px;
    line-height: 1;
    margin-bottom: 20px;
  }
  .details__licence {
    font-size: 13px;
    font-weight: 500;
    margin-bottom: 34px;
  }
  .contact {
    list-style: none;
  }
  .contact__item {
    display: flex;
    align-items: center;
    gap: 7px;
    font-size: 13px;
    margin-bottom: 10px;
  }
  .contact__item--email {
    font-size: 9.6px;
  }
  .contact__icon {
    flex: none;
    width: 13px;
    height: 13px;
    fill: var(--brand-blue);
  }
</style>
</head>
<body>
<main class="canvas">

  <section class="card card--front" aria-label="Card front">
    <div class="brand">
      <span class="brand__dot"></span>
      <p class="brand__name">Quandor<small>Plumbing Solutions</small></p>
    </div>
  </section>

  <section class="card card--back" aria-label="Card back">
    <div class="brand">
      <span class="brand__dot"></span>
      <p class="brand__name">Quandor<small>Plumbing Solutions</small></p>
    </div>

    <span class="divider"></span>

    <div class="details">
      <h1 class="details__name">Felix</h1>
      <p class="details__licence">Licence number 728093K</p>
      <ul class="contact">
        <li class="contact__item">
          <svg class="contact__icon" viewBox="0 0 24 24" aria-hidden="true">
            <path d="M6.6 10.8a15.1 15.1 0 0 0 6.6 6.6l2.2-2.2a1 1 0 0 1 1-.25 11.4 11.4 0 0 0 3.6.57 1 1 0 0 1 1 1V20a1 1 0 0 1-1 1A17 17 0 0 1 3 4a1 1 0 0 1 1-1h3.5a1 1 0 0 1 1 1c0 1.25.2 2.45.57 3.57a1 1 0 0 1-.25 1z"/>
          </svg>
          <span>0461 539 207</span>
        </li>
        <li class="contact__item contact__item--email">
          <svg class="contact__icon" viewBox="0 0 24 24" aria-hidden="true">
            <path d="M2 5h20v14H2z M4 7v.4l8 5.2 8-5.2V7z" fill-rule="evenodd"/>
          </svg>
          <span>quandorplumbingsolutions@mailbrook.example</span>
        </li>
      </ul>
    </div>
  </section>

</main>
</body>
</html>
```